Coastal Learner Bureau business cards

Australian company about to start offering its services. We recruit international students to come to study English, vocational education and postgraduate courses in Australia. We help them find the institution and select the right city they want to come to Australia. We are a young, online oriented and supportive agency. Our clients are between 18 and 35 years old, mainly University students, young professionals or people with work experience. We provide much more information that any other agency offer. We administrate a Facebook group with more than 11.000 members that daily ask questions about general information when coming to Australia, while they are here and even after they leave the country

Target Market(s)

International students from South America, Central America and Europe

Industry/Entity Type

Student

Contact Information for Business Card

Tomas Bilbrea
Managing Director
tomas@kelvarin.com.au
www.kelvoria.com.au
+61 491058264
Melbourne, Australia

Font styles to use
Serif
Sans Serif

Colors

Designer to choose colors to be used in the design.

Requirements
Must have
• Horizontal design
• Standard business card size and shape. If font uses green or yellow colours, they will have to match the ones from the logo
Nice to have
• UPDATE: Use the contents of the green image to design one of the card sides. Use our logo in the background of that side as watermark.
• Passport image, or immigration stamps. A picture of the Yarra River (from Melbourne) would be cool as well.
Should not have
• Non-standard business card size and shape
• Not black as the background colour of any sides as we are not a VIP agency or a hight class service. We are orientes to young people and they like colours, pictures, something attractive.
• Vertical design
• NO YELLOW or BLACK AS THE BACKGROUND COLOUR OF ANY SIDE OF THE BIZ CARD

```html
<!DOCTYPE html>
<html lang="en">
<head>
<meta charset="utf-8">
<title>Coastal Learner Bureau – Business Cards</title>
<link rel="stylesheet" href="https://fonts.googleapis.com/css2?family=Open+Sans:wght@400;600&display=swap">
<style>
  :root {
    --green: #116141;
    --green-dark: #0c4a31;
    --yellow: #e8b81f;
    --white: #ffffff;
    --ink: #1d1d1d;
    --stage: #6b7377;
    --stage-light: #8a9296;
  }
  * { box-sizing: border-box; margin: 0; padding: 0; }
  html, body { width: 1200px; height: 900px; overflow: hidden; }
  body {
    background: radial-gradient(ellipse at 60% 55%, var(--stage-light), var(--stage));
    font-family: "Open Sans", Arial, sans-serif;
    position: relative;
  }
  .card {
    position: absolute;
    left: 300px;
    width: 600px;
    height: 343px;
    border-radius: 18px;
    overflow: hidden;
    box-shadow: 0 10px 28px rgba(0,0,0,.35);
  }
  .card--front { top: 70px; background: var(--white); }
  .card--back { top: 487px; background: var(--green); }

  .front-shape { position: absolute; inset: 0; width: 100%; height: 100%; }

  .brand {
    position: absolute;
    display: flex;
    align-items: center;
    gap: 10px;
    font-weight: 600;
    line-height: 1.1;
  }
  .brand__mark { width: 14px; height: 14px; border-radius: 50%; flex: none; }
  .card--front .brand { left: 58px; top: 62px; color: var(--green); font-size: 26px; width: 260px; }
  .card--front .brand__mark { background: var(--yellow); }

  .contact {
    position: absolute;
    left: 34px;
    bottom: 52px;
    list-style: none;
    font-size: 14px;
    color: var(--ink);
  }
  .contact li { display: flex; align-items: center; gap: 10px; margin-top: 7px; }
  .contact svg { width: 18px; height: 18px; flex: none; }

  .name-band {
    position: absolute;
    right: 0;
    top: 44px;
    width: 270px;
    height: 64px;
    background: var(--yellow);
    clip-path: polygon(10% 0, 100% 0, 100% 100%, 0 100%);
    padding: 9px 0 0 52px;
    color: var(--ink);
  }
  .name-band__name { font-size: 22px; font-weight: 400; display: block; line-height: 1.2; }
  .name-band__role { font-size: 10px; font-weight: 600; display: block; margin-left: 14px; }

  .city-badge {
    position: absolute;
    right: 120px;
    top: 168px;
    width: 56px;
    height: 56px;
  }
  .city {
    position: absolute;
    right: 92px;
    bottom: 34px;
    color: var(--white);
    font-size: 16px;
  }

  .card--back .brand {
    left: 50%;
    top: 120px;
    transform: translateX(-50%);
    color: var(--white);
    font-size: 36px;
    white-space: nowrap;
  }
  .card--back .brand__mark { background: var(--white); width: 18px; height: 18px; }
  .card--back .site {
    position: absolute;
    left: 0; right: 0;
    bottom: 60px;
    text-align: center;
    color: var(--white);
    font-size: 16px;
  }
</style>
</head>
<body>

<section class="card card--front" aria-label="Business card front">
  <svg class="front-shape" viewBox="0 0 600 343" preserveAspectRatio="none" aria-hidden="true">
    <polygon points="350,0 600,0 600,343 205,343" fill="var(--green)"/>
  </svg>

  <div class="brand"><span class="brand__mark"></span>Coastal Learner Bureau</div>

  <ul class="contact">
    <li>
      <svg viewBox="0 0 18 18" aria-hidden="true"><rect width="18" height="18" rx="2" fill="var(--green)"/><path d="M6 4.5l2 2-1.2 1.3a7 7 0 0 0 3.4 3.4L11.5 10l2 2-1.3 1.5C8.5 13.5 4.5 9.5 4.5 5.8z" fill="#fff"/></svg>
      +61 491058264
    </li>
    <li>
      <svg viewBox="0 0 18 18" aria-hidden="true"><rect width="18" height="18" rx="2" fill="var(--green)"/><rect x="4" y="5.5" width="10" height="7" fill="none" stroke="#fff" stroke-width="1.2"/><path d="M4 5.5l5 4 5-4" fill="none" stroke="#fff" stroke-width="1.2"/></svg>
      tomas@kelvarin.com.au
    </li>
    <li>
      <svg viewBox="0 0 18 18" aria-hidden="true"><rect width="18" height="18" rx="2" fill="var(--green)"/><circle cx="9" cy="9" r="4.8" fill="none" stroke="#fff" stroke-width="1.1"/><ellipse cx="9" cy="9" rx="2" ry="4.8" fill="none" stroke="#fff" stroke-width="1"/><path d="M4.2 9h9.6" stroke="#fff" stroke-width="1"/></svg>
      www.kelvoria.com.au
    </li>
  </ul>

  <div class="name-band">
    <span class="name-band__name">Tomas Bilbrea</span>
    <span class="name-band__role">Managing Director</span>
  </div>

  <svg class="city-badge" viewBox="0 0 56 56" role="img" aria-label="City badge">
    <circle cx="28" cy="28" r="26" fill="var(--ink)"/>
    <circle cx="28" cy="28" r="21" fill="none" stroke="var(--green)" stroke-width="2"/>
    <rect x="2" y="23" width="52" height="10" fill="var(--ink)"/>
  </svg>
  <p class="city">Melbourne, Australia</p>
</section>

<section class="card card--back" aria-label="Business card back">
  <div class="brand"><span class="brand__mark"></span>Coastal Learner Bureau</div>
  <p class="site">www.kelvoria.com.au</p>
</section>

</body>
</html>
```